Harborline Outpost Registry needs a web design

We are launching a new website and need a web design. The website is going to list every military base and installment around the world with information on each base such as a description of the base, the history of the base, contact information at the base, address, lat/long of the base, and any other relevant information including images of the base. We need a home page with navigation menu and the design of the military base page so that every military base page is formatted the same for the referenced information. We have included an example of the content that may be found on the base page(s). We are also going to have the information available in spanish.

We also wanted to mention we will be building this website in wordpress.

We also wanted to note that in the format of each base page, we will have a frequently asked questions section with answers.

```html
<!DOCTYPE html>
<html lang="en">
<head>
<meta charset="utf-8">
<title>Harborline Outpost Registry</title>
<link href="https://fonts.googleapis.com/css2?family=Barlow:ital,wght@0,400;0,500;0,600;0,700;1,400;1,500&family=Poppins:wght@700;800&family=Roboto:wght@400;500;700&display=swap" rel="stylesheet">
<style>
:root{
  --olive:#4a5425;
  --olive-light:#6b7640;
  --ink:#262626;
  --muted:#555;
  --white:#fff;
  --star:#f3b71b;
  --footer:#0f0f0d;
  --hero-a:#2a1518;
  --hero-b:#6e1e22;
  --line:#d7d7d7;
}
*{box-sizing:border-box;margin:0;padding:0}
html,body{width:1200px;height:2539px;overflow:hidden}
body{position:relative;font-family:"Barlow",sans-serif;color:var(--ink);background:var(--white)}
a{color:inherit;text-decoration:none}

/* hero */
.hero{position:absolute;left:0;top:0;width:1200px;height:738px;
  background:radial-gradient(ellipse at 50% 40%,#8a2a2c 0%,transparent 60%),linear-gradient(180deg,#3a2226 0%,var(--hero-b) 35%,#4d171a 70%,var(--hero-a) 100%)}
.topbar{position:absolute;left:0;top:0;width:1200px;height:85px;background:rgba(20,14,16,.55);border-bottom:1px solid rgba(255,255,255,.08)}
.brand{position:absolute;left:111px;top:14px;color:var(--white);font-family:"Roboto",sans-serif;font-weight:700;font-size:24px;line-height:30px}
.nav{position:absolute;left:496px;top:32px;display:flex;gap:29px;color:var(--white);font-size:15px;font-weight:500}
.nav .active{position:relative}
.nav .active::after{content:"";position:absolute;left:-2px;right:-2px;top:46px;height:3px;background:var(--white)}
.lang{position:absolute;left:887px;top:27px;display:flex;align-items:center;gap:6px;color:var(--white);font-size:15px;font-weight:500}
.lang .flag{width:30px;height:30px;border-radius:50%;background:linear-gradient(180deg,#c8323a 0 14%,#fff 14% 28%,#c8323a 28% 42%,#fff 42% 56%,#c8323a 56% 70%,#fff 70% 84%,#c8323a 84%)}
.search-link{position:absolute;left:1011px;top:32px;display:flex;gap:12px;align-items:center;color:var(--white);font-size:15px;font-weight:500}
.follow{position:absolute;left:48px;top:262px;width:20px}
.follow span{display:block;writing-mode:vertical-rl;transform:rotate(180deg);color:var(--white);font-size:11px;letter-spacing:3px;font-weight:600}
.follow i{display:block;width:1px;height:62px;background:var(--white);margin:14px 0 0 9px}
.follow b{display:block;width:9px;height:9px;border-radius:50%;background:var(--white);margin:20px 0 0 5px}
.hero-title{position:absolute;left:0;top:238px;width:1200px;text-align:center;color:var(--white);font-family:"Poppins",sans-serif;font-weight:700;font-size:58px;line-height:68px}
.search-box{position:absolute;left:322px;top:386px;width:556px;height:55px;background:var(--white);display:flex;align-items:center;padding:0 6px 0 22px}
.search-box .ph{flex:1;margin-left:16px;color:#666;font-size:14px}
.search-box .btn{width:131px;height:42px;background:var(--olive);color:var(--white);font-weight:700;font-size:15px;display:flex;align-items:center;justify-content:center;gap:6px}

/* categories */
.cats{position:absolute;left:113px;top:633px;display:flex;gap:14px}
.cat{width:184px;height:184px;background:var(--olive);color:var(--white);text-align:center;padding-top:28px}
.cat .art{width:84px;height:84px;margin:0 auto;background:var(--olive-light);border-radius:4px}
.cat p{margin-top:18px;font-size:18px;font-weight:600}

/* popular */
.sec-title{position:absolute;left:0;width:1200px;text-align:center;font-family:"Poppins",sans-serif;font-weight:700;font-size:41px;line-height:56px}
.cards{position:absolute;left:113px;top:1001px;display:flex;gap:28px}
.card{width:307px;height:500px;border:1px solid var(--line);position:relative}
.card .photo{height:242px}
.p1{background:linear-gradient(180deg,#e9a55a 0%,#f2c77a 25%,#5d7fa6 55%,#2e5d8c 100%)}
.p2{background:linear-gradient(135deg,#b8c3cc 0%,#7e8b96 45%,#3a3f46 100%)}
.p3{background:linear-gradient(180deg,#d7e1e6 0%,#8e9ea6 40%,#6e9a3c 70%,#4b7a2a 100%)}
.card .body{padding:22px 27px 0}
.card h3{font-size:19px;font-weight:600;color:#222}
.stars{margin-top:12px;display:flex;gap:3px}
.card .desc{margin-top:12px;font-size:13.5px;color:var(--muted)}
.row{display:flex;margin-top:14px;font-size:13.5px;color:var(--muted);line-height:21px}
.row svg{margin:5px 8px 0 0;flex:none}
.row strong{font-weight:500;color:#333;margin-left:9px}
.links{position:absolute;left:28px;right:31px;bottom:17px;display:flex;justify-content:space-between;font-size:13.5px;font-weight:600;text-decoration:underline}
.arrow{position:absolute;top:1232px;width:41px;height:41px;border-radius:50%;background:var(--white);box-shadow:0 2px 8px rgba(0,0,0,.15);display:flex;align-items:center;justify-content:center}

/* reviews */
.reviews{position:absolute;left:0;top:1603px;width:1200px;height:508px;
  background:radial-gradient(circle at 15% 30%,#3f4a1f 0 12%,transparent 13%),radial-gradient(circle at 70% 20%,#2a2416 0 10%,transparent 11%),radial-gradient(circle at 40% 75%,#4b5326 0 14%,transparent 15%),radial-gradient(circle at 88% 70%,#2b2f16 0 12%,transparent 13%),linear-gradient(135deg,#3a3b1d,#2c2a18 50%,#3d4420)}
.review{position:absolute;top:185px;width:445px;color:var(--white)}
.review .head{display:flex;justify-content:space-between;align-items:center}
.review .name{font-size:18px;font-weight:600}
.review p{margin-top:18px;font-style:italic;font-size:14px;line-height:21.5px;text-align:justify}
.review .meta{margin-top:14px;display:flex;gap:44px;font-size:14px;align-items:center;height:24px}
.review .meta span{display:flex;gap:4px;align-items:center}
.quote{position:absolute;right:0;bottom:-34px;font-family:"Poppins",sans-serif;font-weight:800;font-size:92px;line-height:92px;color:rgba(255,255,255,.3)}
.dots{position:absolute;left:578px;top:422px;display:flex;gap:7px}
.dots i{width:10px;height:10px;border-radius:50%;background:rgba(255,255,255,.6)}
.dots i.on{background:var(--white)}

/* footer */
.footer{position:absolute;left:0;top:2111px;width:1200px;height:428px;background:var(--footer);color:var(--white);font-family:"Roboto",sans-serif}
.f-brand{position:absolute;left:111px;top:98px;font-weight:700;font-size:24px;line-height:30px}
.socials{position:absolute;left:112px;top:185px;display:flex;gap:8px}
.socials i{width:33px;height:34px;background:var(--white);display:flex;align-items:center;justify-content:center}
.socials i::after{content:"";width:8px;height:8px;border-radius:50%;background:var(--footer)}
.f-col h4{font-size:20px;font-weight:500}
.f-col{position:absolute;top:100px}
.f-list{margin-top:20px;list-style:none;font-size:16px;line-height:28.5px}
.f-list li::before{content:"»";margin-right:12px}
.contact{margin-top:22px;font-size:16px;line-height:28px}
.contact div{display:flex;gap:14px;margin-bottom:25px}
.contact svg{flex:none;margin-top:5px}
.field{width:266px;height:41px;background:var(--white);margin-top:12px;color:#999;font-size:12px;padding:12px 13px}
.submit{margin-top:12px;margin-left:-4px;width:110px;height:41px;border-radius:21px;background:var(--olive);font-weight:700;font-size:14px;display:flex;align-items:center;justify-content:center}
.f-rule{position:absolute;left:112px;top:355px;width:977px;height:1px;background:#444}
.copy{position:absolute;left:0;top:382px;width:1200px;text-align:center;font-size:14px}
</style>
</head>
<body>

<section class="hero" role="img" aria-label="Soldiers in silhouette before a waving national flag">
  <div class="topbar">
    <div class="brand">Harborline Outpost<br>Registry</div>
    <nav class="nav"><a class="active">Home</a><a>About</a><a>Services</a><a>Blog</a><a>Contact</a></nav>
    <div class="lang"><span class="flag"></span>Eng
      <svg width="9" height="6" viewBox="0 0 9 6"><path d="M1 1l3.5 3.5L8 1" stroke="#fff" fill="none" stroke-width="1.5"/></svg></div>
    <div class="search-link"><svg width="15" height="15" viewBox="0 0 15 15"><circle cx="6" cy="6" r="4.5" stroke="#fff" stroke-width="2" fill="none"/><path d="M9.5 9.5l4 4" stroke="#fff" stroke-width="2.2"/></svg>Search</div>
  </div>
  <div class="follow"><span>FOLLOW US</span><i></i><b></b><b></b><b></b></div>
  <h1 class="hero-title">HARBORLINE OUTPOST<br>REGISTRY</h1>
  <div class="search-box">
    <svg width="10" height="14" viewBox="0 0 10 14"><path d="M5 0a5 5 0 0 0-5 5c0 3.5 5 9 5 9s5-5.5 5-9a5 5 0 0 0-5-5zm0 7a2 2 0 1 1 0-4 2 2 0 0 1 0 4z" fill="#555"/></svg>
    <span class="ph">Enter your location</span>
    <span class="btn"><svg width="13" height="13" viewBox="0 0 15 15"><circle cx="6" cy="6" r="4.5" stroke="#fff" stroke-width="2" fill="none"/><path d="M9.5 9.5l4 4" stroke="#fff" stroke-width="2.2"/></svg>SEARCH</span>
  </div>
</section>

<div class="cats">
  <div class="cat"><div class="art" role="img" aria-label="Line illustration of a barracks hut and watchtower"></div><p>Duis aute irure</p></div>
  <div class="cat"><div class="art" role="img" aria-label="Line illustration of a field tent with a flag"></div><p>Duis aute irure</p></div>
  <div class="cat"><div class="art" role="img" aria-label="Line illustration of a lookout tower"></div><p>Duis aute irure</p></div>
  <div class="cat"><div class="art" role="img" aria-label="Line illustration of a uniformed service member"></div><p>Duis aute irure</p></div>
  <div class="cat"><div class="art" role="img" aria-label="Line illustration of a hand holding a rank badge"></div><p>Duis aute irure</p></div>
</div>

<h2 class="sec-title" style="top:906px">POPULAR THIS WEEK</h2>

<div class="arrow" style="left:36px"><svg width="8" height="12" viewBox="0 0 8 12"><path d="M6 1L1 6l5 5" stroke="#222" stroke-width="1.6" fill="none"/></svg></div>
<div class="arrow" style="left:1123px"><svg width="8" height="12" viewBox="0 0 8 12"><path d="M2 1l5 5-5 5" stroke="#222" stroke-width="1.6" fill="none"/></svg></div>

<div class="cards">
  <article class="card">
    <div class="photo p1" role="img" aria-label="Coastal village with white buildings at sunset"></div>
    <div class="body">
      <h3>Fort Calder Military Base:</h3>
      <div class="stars"><svg width="80" height="13" viewBox="0 0 80 13"><g fill="none" stroke="#f3b71b"><path id="s" d="M6.5 1l1.6 3.6 3.9.4-3 2.6.9 3.9-3.4-2-3.4 2 .9-3.9-3-2.6 3.9-.4z"/><use href="#s" x="16.5"/><use href="#s" x="33"/><use href="#s" x="49.5"/><use href="#s" x="66"/></g></svg></div>
      <p class="desc">History, Facilities, and Support Services</p>
      <div class="row"><svg width="11" height="11" viewBox="0 0 11 11"><path d="M2 0l2 2.5-1 1.5c.8 1.6 2 2.8 3.5 3.5l1.5-1 2.5 2L9 11C4 11 0 7 0 2z" fill="#444"/></svg>Phone :<strong>(555) 014-2290</strong></div>
      <div class="row"><svg width="9" height="12" viewBox="0 0 10 14"><path d="M5 0a5 5 0 0 0-5 5c0 3.5 5 9 5 9s5-5.5 5-9a5 5 0 0 0-5-5zm0 7a2 2 0 1 1 0-4 2 2 0 0 1 0 4z" fill="#444"/></svg>Location :<strong>Fort Calder, KY,<br>United States</strong></div>
    </div>
    <div class="links"><a>Directions</a><a>Email</a></div>
  </article>
  <article class="card">
    <div class="photo p2" role="img" aria-label="Travellers with luggage walking through an airport terminal"></div>
    <div class="body">
      <h3>Fort Calder Military Base:</h3>
      <div class="stars"><svg width="80" height="13" viewBox="0 0 80 13"><g fill="none" stroke="#f3b71b"><use href="#s"/><use href="#s" x="16.5"/><use href="#s" x="33"/><use href="#s" x="49.5"/><use href="#s" x="66"/></g></svg></div>
      <p class="desc">History, Facilities, and Support Services</p>
      <div class="row"><svg width="11" height="11" viewBox="0 0 11 11"><path d="M2 0l2 2.5-1 1.5c.8 1.6 2 2.8 3.5 3.5l1.5-1 2.5 2L9 11C4 11 0 7 0 2z" fill="#444"/></svg>Phone :<strong>(555) 014-2290</strong></div>
      <div class="row"><svg width="9" height="12" viewBox="0 0 10 14"><path d="M5 0a5 5 0 0 0-5 5c0 3.5 5 9 5 9s5-5.5 5-9a5 5 0 0 0-5-5zm0 7a2 2 0 1 1 0-4 2 2 0 0 1 0 4z" fill="#444"/></svg>Location :<strong>Fort Calder, KY,<br>United States</strong></div>
    </div>
    <div class="links"><a>Directions</a><a>Email</a></div>
  </article>
  <article class="card">
    <div class="photo p3" role="img" aria-label="City skyline behind a green rooftop garden"></div>
    <div class="body">
      <h3>Fort Calder Military Base:</h3>
      <div class="stars"><svg width="80" height="13" viewBox="0 0 80 13"><g fill="none" stroke="#f3b71b"><use href="#s"/><use href="#s" x="16.5"/><use href="#s" x="33"/><use href="#s" x="49.5"/><use href="#s" x="66"/></g></svg></div>
      <p class="desc">History, Facilities, and Support Services</p>
      <div class="row"><svg width="11" height="11" viewBox="0 0 11 11"><path d="M2 0l2 2.5-1 1.5c.8 1.6 2 2.8 3.5 3.5l1.5-1 2.5 2L9 11C4 11 0 7 0 2z" fill="#444"/></svg>Phone :<strong>(555) 014-2290</strong></div>
      <div class="row"><svg width="9" height="12" viewBox="0 0 10 14"><path d="M5 0a5 5 0 0 0-5 5c0 3.5 5 9 5 9s5-5.5 5-9a5 5 0 0 0-5-5zm0 7a2 2 0 1 1 0-4 2 2 0 0 1 0 4z" fill="#444"/></svg>Location :<strong>Fort Calder, KY,<br>United States</strong></div>
    </div>
    <div class="links"><a>Directions</a><a>Email</a></div>
  </article>
</div>

<section class="reviews" role="img" aria-label="Camouflage pattern background">
  <h2 class="sec-title" style="top:118px;color:#fff">RECENT REVIEWS</h2>
  <div class="review" style="left:113px">
    <div class="head"><svg width="96" height="15" viewBox="0 0 96 15"><g fill="#f3b71b"><path id="f" d="M7 .5l2 4.4 4.7.5-3.5 3.2 1 4.7L7 11 2.8 13.3l1-4.7L.3 5.4 5 4.9z"/><use href="#f" x="20"/><use href="#f" x="40"/><use href="#f" x="60"/><use href="#f" x="80"/></g></svg><span class="name">John Doe</span></div>
    <p>“Lorem ipsum dolor sit amet, consectetur adipiscing elit, sed do eiusmod tempor incididunt ut labore et dolore magna aliqua. Ut enim ad minim veniam, quis nostrud exercitation ullamco laboris nisi ut aliquip ex ea commodo consequat. Duis aute irure dolor in reprehenderit in voluptate velit esse cillum dolore eu fugiat nulla pariatur.”</p>
    <div class="meta"><span><svg width="13" height="13" viewBox="0 0 13 13"><rect x="1" y="2" width="11" height="10" fill="none" stroke="#fff"/><path d="M1 5h11M4 1v2M9 1v2" stroke="#fff"/></svg>Jan 22</span><span><svg width="13" height="13" viewBox="0 0 13 13"><circle cx="6.5" cy="6.5" r="5.5" fill="none" stroke="#fff" stroke-width="1.5"/><path d="M6.5 3.5v3h2" stroke="#fff" stroke-width="1.5" fill="none"/></svg>10:48</span></div>
    <span class="quote">“</span>
  </div>
  <div class="review" style="left:644px">
    <div class="head"><svg width="96" height="15" viewBox="0 0 96 15"><g fill="#f3b71b"><use href="#f"/><use href="#f" x="20"/><use href="#f" x="40"/><use href="#f" x="60"/><use href="#f" x="80"/></g></svg><span class="name">John Doe</span></div>
    <p>“Lorem ipsum dolor sit amet, consectetur adipiscing elit, sed do eiusmod tempor incididunt ut labore et dolore magna aliqua. Ut enim ad minim veniam, quis nostrud exercitation ullamco laboris nisi ut aliquip ex ea commodo consequat. Duis aute irure dolor in reprehenderit in voluptate velit esse cillum dolore eu fugiat nulla pariatur.”</p>
    <div class="meta"><span><svg width="13" height="13" viewBox="0 0 13 13"><rect x="1" y="2" width="11" height="10" fill="none" stroke="#fff"/><path d="M1 5h11M4 1v2M9 1v2" stroke="#fff"/></svg>Jan 22</span><span><svg width="13" height="13" viewBox="0 0 13 13"><circle cx="6.5" cy="6.5" r="5.5" fill="none" stroke="#fff" stroke-width="1.5"/><path d="M6.5 3.5v3h2" stroke="#fff" stroke-width="1.5" fill="none"/></svg>10:48</span></div>
    <span class="quote">“</span>
  </div>
  <div class="dots"><i></i><i class="on"></i><i></i></div>
</section>

<footer class="footer">
  <div class="f-brand">Harborline Outpost<br>Registry</div>
  <div class="socials"><i></i><i></i><i></i><i></i></div>
  <div class="f-col" style="left:397px"><h4>Information</h4>
    <ul class="f-list"><li>Home</li><li>Services</li><li>Features</li><li>About us</li><li>Blog</li><li>Contact us</li></ul></div>
  <div class="f-col" style="left:577px"><h4>Contact Us</h4>
    <div class="contact">
      <div><svg width="14" height="18" viewBox="0 0 10 14"><path d="M5 0a5 5 0 0 0-5 5c0 3.5 5 9 5 9s5-5.5 5-9a5 5 0 0 0-5-5zm0 7a2 2 0 1 1 0-4 2 2 0 0 1 0 4z" fill="#fff"/></svg><span style="margin-left:4px">123, Lorem Ipsum<br>simply dummy</span></div>
      <div style="margin-top:10px"><svg width="19" height="19" viewBox="0 0 11 11"><path d="M2 0l2 2.5-1 1.5c.8 1.6 2 2.8 3.5 3.5l1.5-1 2.5 2L9 11C4 11 0 7 0 2z" fill="#fff"/></svg><span>+1 888 888 8888</span></div>
      <div><svg width="21" height="14" viewBox="0 0 21 14"><rect x=".5" y=".5" width="20" height="13" fill="none" stroke="#fff"/><path d="M.5.5l10 7 10-7" stroke="#fff" fill="none"/></svg><span>info@harborline-registry.com</span></div>
    </div></div>
  <div class="f-col" style="left:822px"><h4>Newsletter</h4>
    <div class="field" style="margin-top:28px">Your Name</div>
    <div class="field">Enter Your Email Address</div>
    <div class="submit">SUBMIT</div></div>
  <div class="f-rule"></div>
  <p class="copy">© Copyrights Company name 2023. All rights reserved | Privacy policy | Terms Condition</p>
</footer>

</body>
</html>
```